Public Relations Agency Seeks Wordpress Design and Coding

TRELVOX Studio is a public relations agency specializing in media relations, public affairs and marketing communication.

The site should display the following visual characteristics: professionalism, trustworthiness, high-tech focus, clear and concise design.

The desired colors are royal blue, gray and hints of red.

Design look/feel inspired by this site: http://brightpathgatherings.example/

Specifications:

1. Navigation/Pages/Index:

HOME

ABOUT US

SERVICES

NEWS

CONTACT

---

2. Functionality of/content for each page:

- Home
o Dominant photo (professional, edgy, innovative)
o Simple, straightforward access to/from “Home” from other pages
o Includes logo (attached) and tagline "Unleash the power of communication"
o Direct link to “CONTACT”
o Links to social media accounts: Facebook, Twitter, LinkedIn

- About Us

o Company profile blurb
o President’s photo with short bio

- Services
o Public Relations
 Strategic communication
 Brand and reputation management
 Community relations
o Media Relations
 News coverage and contacts
 Media training and interview skills
 Crisis communications
o Congressional Affairs
 Public affairs
 Public policy
 Legislative strategy
o Mass Communication
 Speechwriting
 Presentation creation
 Social media
o Marketing Communications
 Business collateral material
 Promotional campaigns
 Special events and tradeshows

- News
o Blog-like page to post information and/or share news from other sites

- Contact
o Standard “Contact Us” form (Name, Email, Phone, Message)
o Direct Contact
 (407) 555-0164
 Marisol@TRELVOXstudio.example

Target Market(s)

Small to large businesses specializing in high technology, defense/military, medicine/healthcare, and wide array of professional services.

Industry/Entity Type

Marketing

Font styles to use
Serif
Sans Serif

Colors
0555a3
ec2027
edf3f7

Requirements
Must have
• -- Project reqires DESIGN - and - fully CODED.

-- Strong SEO

-- Optimized for mobile viewing

Thank you!

```html
<!DOCTYPE html>
<html lang="en">
<head>
<meta charset="utf-8">
<title>TRELVOX Studio – Unleash the power of communication</title>
<link rel="stylesheet" href="https://fonts.googleapis.com/css2?family=PT+Serif:ital@0;1&family=Roboto:wght@400;500;700&family=PT+Sans:wght@400;700&display=swap">
<style>
:root{
  --blue:#0555a3;
  --blue-dark:#044a8f;
  --red:#ec2027;
  --pale:#edf3f7;
  --grey-text:#5f5f5f;
  --dark:#2b2b2b;
  --line:#dcdcdc;
  --white:#ffffff;
}
*{box-sizing:border-box;margin:0;padding:0}
html,body{width:1200px;height:2624px;overflow:hidden;background:var(--white)}
body{position:relative;font-family:"PT Sans",Arial,sans-serif;color:var(--grey-text)}
.abs{position:absolute}

/* header */
.topline{left:0;top:0;width:1200px;height:4px;background:var(--blue)}
.site-header{left:0;top:4px;width:1200px;height:92px;background:var(--white)}
.brand{left:140px;top:28px;display:flex;align-items:center;gap:10px}
.brand-mark{width:14px;height:14px;background:var(--blue)}
.brand-name{font-family:"Roboto",sans-serif;font-weight:500;font-size:28px;color:#555a60;letter-spacing:1px}
.main-nav{left:597px;top:14px;display:flex;height:55px;align-items:center}
.main-nav a{font-family:"Roboto",sans-serif;font-size:14px;color:#333;text-decoration:none;margin-right:54px}
.main-nav a.active{background:var(--blue);color:var(--white);height:55px;width:54px;display:flex;align-items:center;justify-content:center;border-bottom:4px solid var(--red);margin-right:46px}

/* hero */
.hero{left:0;top:96px;width:1200px;height:548px;background:linear-gradient(90deg,#e4e9ef 0%,#c3ccd6 30%,#b7c1cc 50%,#d6dde4 70%,#f0f3f6 100%)}
.tagline{left:143px;top:172px;font-family:"PT Serif",serif;font-weight:400}
.tagline em{display:block;font-size:35px;color:#555;font-style:italic;font-weight:400}
.tagline strong{display:block;font-size:42px;color:var(--red);font-weight:400;margin-top:2px;letter-spacing:.5px}
.hero-dots{left:141px;top:590px;display:flex;gap:6px}
.hero-dots span{width:10px;height:10px;border-radius:50%;background:var(--white)}
.hero-dots span.on{background:var(--red)}

/* section titles */
.section-title{left:0;width:1200px;text-align:center;font-family:"Roboto",sans-serif;font-weight:700;font-size:23px;color:#444}
.section-title::after{content:"";display:block;width:48px;height:3px;background:var(--red);margin:8px auto 0}
.section-title.on-blue{color:var(--white)}

/* about */
.president-photo{left:140px;top:736px;width:241px;height:238px;border:6px solid #f1f1f1;box-shadow:0 0 0 1px var(--line);background:linear-gradient(135deg,#6d7178,#c14a4f 70%,#b8333a)}
.about-copy{left:430px;top:738px;width:630px;font-size:12px;line-height:24px}
.about-list{list-style:none;margin-top:14px}
.about-list li{position:relative;padding-left:18px;margin-bottom:6px}
.about-list li::before{content:"";position:absolute;left:0;top:8px;border-left:6px solid var(--red);border-top:4px solid transparent;border-bottom:4px solid transparent}

/* services */
.service-card{top:1088px;width:290px;height:357px;border:1px solid var(--line);background:var(--white)}
.service-card .thumb{position:absolute;left:13px;top:13px;width:262px;height:155px}
.service-card h3{position:absolute;left:18px;top:184px;font-family:"Roboto",sans-serif;font-weight:400;font-size:15px;color:#222}
.service-card p{position:absolute;left:18px;top:214px;width:254px;font-size:12px;line-height:23px;text-align:justify}
.service-card .read-more{position:absolute;left:18px;top:318px;font-size:12px;color:#777;display:flex;align-items:center;gap:8px}
.read-more i{width:9px;height:9px;border-radius:50%;background:var(--red);display:block}

/* portfolio */
.portfolio{left:0;top:1488px;width:1200px;height:378px;background:linear-gradient(160deg,#0a62b5 0%,var(--blue) 45%,var(--blue-dark) 100%)}
.portfolio-item{top:102px;height:178px}
.portfolio-controls{left:569px;top:315px;display:flex;gap:8px}

/* news */
.news-item{top:1982px;width:260px;text-align:center}
.date-box{width:61px;height:58px;margin:0 auto;background:var(--pale);font-family:"Roboto",sans-serif;font-weight:700;font-size:25px;color:#333;display:flex;align-items:center;justify-content:center;position:relative}
.date-box.current{background:var(--red);color:var(--white)}
.date-box.current::after{content:"";position:absolute;bottom:-8px;left:24px;border-top:8px solid var(--red);border-left:7px solid transparent;border-right:7px solid transparent}
.news-month{margin-top:14px;font-family:"Roboto",sans-serif;font-weight:700;font-size:19px;color:var(--red)}
.news-title{margin-top:12px;font-family:"Roboto",sans-serif;font-weight:700;font-size:18px;color:#222}
.news-text{margin-top:10px;font-size:12px;line-height:21px;color:#333}
.more-btn{display:inline-block;margin-top:14px;width:82px;height:33px;line-height:33px;background:var(--pale);font-family:"Roboto",sans-serif;font-weight:700;font-size:13px;color:#333}
.more-btn.current{background:var(--red);color:var(--white)}

/* footer */
.site-footer{left:0;top:2309px;width:1200px;height:257px;background:var(--blue);color:var(--white)}
.footer-col{top:43px}
.footer-col h4{font-family:"Roboto",sans-serif;font-weight:400;font-size:16px;margin-bottom:20px}
.tweet{position:relative;padding-left:22px;font-size:11px;line-height:18px;width:255px;margin-bottom:16px}
.tweet::before{content:"";position:absolute;left:0;top:4px;width:9px;height:9px;border-radius:50%;background:#2c7bd0}
.footer-links{list-style:none;font-size:11px;line-height:23.5px}
.footer-links li::before{content:"» ";}
.company-details{font-size:11px;line-height:17.5px}
.field{width:229px;height:30px;border:1px solid #cfe0f2;margin-bottom:10px;font-size:11px;padding:7px 12px}
.field.message{height:49px}
.send-btn{display:inline-block;width:46px;height:24px;line-height:24px;background:var(--blue-dark);text-align:center;font-size:11px}
.bottom-bar{left:0;top:2566px;width:1200px;height:58px;background:var(--red);color:var(--white)}
.copyright{left:143px;top:20px;font-size:11px}
.social{left:934px;top:13px;display:flex;gap:14px}
.social span{width:32px;height:32px;border:1.5px solid var(--white);border-radius:50%;display:block}
</style>
</head>
<body>

<div class="abs topline"></div>
<header class="abs site-header">
  <div class="abs brand"><span class="brand-mark"></span><span class="brand-name">TRELVOX Studio</span></div>
  <nav class="abs main-nav">
    <a class="active" href="#">Home</a>
    <a href="#">About Us</a>
    <a href="#">Services</a>
    <a href="#">News</a>
    <a href="#">Contact Us</a>
  </nav>
</header>

<section class="abs hero" role="img" aria-label="Hero photograph: smiling businesswoman in front of a blurred group of professionals"></section>
<h1 class="abs tagline"><em>Unleash the power of</em><strong>COMMUNICATION</strong></h1>
<div class="abs hero-dots"><span class="on"></span><span></span><span></span><span></span></div>

<h2 class="abs section-title" style="top:675px">ABOUT US</h2>
<div class="abs president-photo" role="img" aria-label="Portrait of the agency president"></div>
<div class="abs about-copy">
  <p>Consectetuer adipiscing elit. Aenean commodo ligula eget dolor. Aenean massa. Cum sociis natoque penatibus et magnis dis parturient montes, nascetur ridiculus mus. Donec quam felis, ultricies nec, pellentesque eu, pretium quis, sem. Nulla consequat massa quis enim.</p>
  <ul class="about-list">
    <li>Integer tincidunt. Cras dapibus. Vivamus elementum semper nisi.Consectetuer adipiscing elit.</li>
    <li>Aenean commodo ligula eget dolor. Aenean massa. Cum sociis natoque penatibus .</li>
    <li>Et magnis dis parturient montes, nascetur ridiculus mus.</li>
    <li>Donec quam felis, ultricies nec, pellentesque eu, pretium quis, sem. Nulla consequat massa quis enim.</li>
    <li>Donec pede justo, fringilla vel, aliquet nec, vulputate eget, arcu.</li>
  </ul>
</div>

<h2 class="abs section-title" style="top:1014px">OUR SERVICES</h2>
<article class="abs service-card" style="left:140px">
  <div class="thumb" role="img" aria-label="Camera crew filming a speaker at a press event" style="background:linear-gradient(135deg,#d9d9d9,#5b5450 60%,#3a3532)"></div>
  <h3>Media Relations</h3>
  <p>Consectetuer adipiscing elit. Aenean commodo ligula eget dolor. Aenean massa. Cum sociis natoque penatibus et magnis dis parturient montes, nascetur</p>
  <span class="read-more"><i></i>Read More</span>
</article>
<article class="abs service-card" style="left:455px">
  <div class="thumb" role="img" aria-label="Business people shaking hands in a bright office" style="background:linear-gradient(135deg,#e8edf2,#a9b6c4 60%,#5e6c7c)"></div>
  <h3>Public Affairs</h3>
  <p>Consectetuer adipiscing elit. Aenean commodo ligula eget dolor. Aenean massa. Cum sociis natoque penatibus et magnis dis parturient montes, nascetur</p>
  <span class="read-more"><i></i>Read More</span>
</article>
<article class="abs service-card" style="left:770px">
  <div class="thumb" role="img" aria-label="Team laughing together around a meeting table" style="background:linear-gradient(135deg,#f1f1f1,#c8b3a3 55%,#6e7d90)"></div>
  <h3>Marketing Communication</h3>
  <p>Consectetuer adipiscing elit. Aenean commodo ligula eget dolor. Aenean massa. Cum sociis natoque penatibus et magnis dis parturient montes, nascetur</p>
  <span class="read-more"><i></i>Read More</span>
</article>

<section class="abs portfolio">
  <h2 class="abs section-title on-blue" style="top:30px">OUR PORTFOLIO</h2>
  <div class="abs portfolio-item" style="left:140px;width:222px;background:#1f1f1f" role="img" aria-label="Silhouettes of a business group">
    <svg class="abs" style="left:78px;top:76px" width="66" height="28" viewBox="0 0 66 28" aria-hidden="true">
      <circle cx="14" cy="14" r="13" fill="#fff"/><circle cx="14" cy="14" r="4" fill="none" stroke="#555" stroke-width="2"/>
      <circle cx="50" cy="14" r="13" fill="#fff"/><circle cx="48" cy="12" r="5" fill="none" stroke="#555" stroke-width="2"/><line x1="52" y1="16" x2="56" y2="20" stroke="#555" stroke-width="2"/>
    </svg>
  </div>
  <div class="abs portfolio-item" style="left:371px;width:222px;background:linear-gradient(135deg,#b8b2aa,#4a4340)" role="img" aria-label="Press photographers with cameras"></div>
  <div class="abs portfolio-item" style="left:602px;width:222px;background:linear-gradient(135deg,#f2efec,#c9a991 60%,#7a685d)" role="img" aria-label="Colleagues reviewing documents at a desk"></div>
  <div class="abs portfolio-item" style="left:833px;width:227px;background:linear-gradient(180deg,#eef2f6,#8e9aa8 60%,#4d5562)" role="img" aria-label="Office towers with people walking below"></div>
  <svg class="abs portfolio-controls" width="60" height="27" viewBox="0 0 60 27" aria-label="Previous and next">
    <circle cx="13" cy="13.5" r="13" fill="#fff"/><polyline points="16,8 10,13.5 16,19" fill="none" stroke="#333" stroke-width="2.5"/>
    <circle cx="47" cy="13.5" r="13" fill="#fff"/><polyline points="44,8 50,13.5 44,19" fill="none" stroke="#333" stroke-width="2.5"/>
  </svg>
</section>

<h2 class="abs section-title" style="top:1896px">LATEST NEWS</h2>
<article class="abs news-item" style="left:141px">
  <div class="date-box current">29</div>
  <div class="news-month">September</div>
  <h3 class="news-title">Lorem Ipsum is simply</h3>
  <p class="news-text">Lorem Ipsum is simply dummy text of the printing and typesetting industry. Lorem Ipsum has been the industry's standard unchanged</p>
  <span class="more-btn current">MORE</span>
</article>
<article class="abs news-item" style="left:468px">
  <div class="date-box">25</div>
  <div class="news-month">September</div>
  <h3 class="news-title">Lorem Ipsum is simply</h3>
  <p class="news-text">Lorem Ipsum is simply dummy text of the printing and typesetting industry. Lorem Ipsum has been the industry's standard unchanged</p>
  <span class="more-btn">MORE</span>
</article>
<article class="abs news-item" style="left:799px">
  <div class="date-box">18</div>
  <div class="news-month">September</div>
  <h3 class="news-title">Lorem Ipsum is simply</h3>
  <p class="news-text">Lorem Ipsum is simply dummy text of the printing and typesetting industry. Lorem Ipsum has been the industry's standard unchanged</p>
  <span class="more-btn">MORE</span>
</article>

<footer class="abs site-footer">
  <div class="abs footer-col" style="left:147px">
    <h4>Latest Tweets</h4>
    <p class="tweet">Vestibulumaccumsan egestibulum eu justo convallis augue estas aenean elit intesque sed. Facilispede estibulum</p>
    <p class="tweet">Vestibulumaccumsan egestibulum eu justo convallis augue estas aenean elit intesque sed. Facilispede estibulum</p>
  </div>
  <div class="abs footer-col" style="left:430px">
    <h4>Navigation</h4>
    <ul class="footer-links"><li>Home</li><li>About Us</li><li>Services</li><li>Contact Us</li><li>Privacy</li><li>News</li></ul>
  </div>
  <div class="abs footer-col" style="left:598px">
    <h4>Company Details</h4>
    <p class="company-details">Company Name<br>Street Name &amp; Number<br>Town<br>Postcode/Zip<br><br>Tel: 0419 555 018<br>Email: info@trelvoxstudio.example</p>
  </div>
  <div class="abs footer-col" style="left:831px">
    <h4>Contact</h4>
    <div class="field">Name</div>
    <div class="field">Email</div>
    <div class="field message">Message</div>
    <span class="send-btn">Send</span>
  </div>
</footer>

<div class="abs bottom-bar">
  <p class="abs copyright">Copyright © 2014 trelvoxstudio | All Rights Reserved</p>
  <div class="abs social" aria-label="Social media links"><span></span><span></span><span></span></div>
</div>

</body>
</html>
```